Cover für Gedichtbuch
Zielgruppe
Das Buch soll jungen und alten Menschen gefallen. Zielgruppe sind aber vor allem junge Leser zwischen 18 und Mitte 20.
Aufgabenstellung
Für das Erstlingswerk von zwei Nachwuchsautoren wird ein Wendecover gesucht. Sprich: Auf der einen Seite stehen Gedichte mit hellen Gedichten (Liebe, Freude, Glück) - die andere Hälfte besteht aus dunklen Gedichten (Tod, Depression). Das Buch soll gedreht werden. Daher sollen die beiden Coverseiten einen Kontrast darstellen.

```html
<!DOCTYPE html>
<html lang="de">
<head>
<meta charset="utf-8">
<title>Dunkle Gedichte – Cover</title>
<link rel="stylesheet" href="https://fonts.googleapis.com/css2?family=Metamorphous&family=Didact+Gothic&display=swap">
<style>
  :root {
    --night: #1b1b1c;
    --band-slate: #3e4a4b;
    --band-mauve: #5a4651;
    --band-rust: #9a3a31;
    --band-ember: #d2472f;
    --field: #262a2a;
    --medallion: #1c4d57;
    --title-gold: #c8a574;
    --author-coral: #d9805f;
  }
  html, body {
    margin: 0;
    padding: 0;
    overflow: hidden;
    background: var(--night);
  }
  .cover {
    position: relative;
    width: 844px;
    height: 1200px;
    overflow: hidden;
    background: var(--night);
  }
  .cover__sweep {
    position: absolute;
    inset: 0;
    width: 844px;
    height: 1200px;
  }
  .medallion {
    position: absolute;
    left: 212px;
    top: 196px;
    width: 412px;
    height: 412px;
    border-radius: 50%;
    background: var(--medallion);
    text-align: center;
  }
  .medallion__title {
    margin: 100px 0 0;
    font-family: "Metamorphous", serif;
    font-weight: 400;
    font-size: 56px;
    line-height: 62px;
    color: var(--title-gold);
  }
  .medallion__rule {
    width: 240px;
    height: 0;
    margin: 34px auto 0;
    border-top: 1.5px solid var(--title-gold);
  }
  .medallion__author {
    margin: 30px 0 0;
    font-family: "Didact Gothic", sans-serif;
    font-size: 22px;
    letter-spacing: 0.5px;
    color: var(--author-coral);
  }
</style>
</head>
<body>
  <main class="cover">
    <svg class="cover__sweep" viewBox="0 0 844 1200" xmlns="http://www.w3.org/2000/svg">
      <path class="band band--slate" fill="var(--band-slate)" d="M0,24 Q620,40 844,240 L844,1200 L0,1200 Z"/>
      <path class="band band--mauve" fill="var(--band-mauve)" d="M0,72 Q620,90 844,364 L844,1200 L0,1200 Z"/>
      <path class="band band--rust" fill="var(--band-rust)" d="M0,120 Q620,140 844,485 L844,1200 L0,1200 Z"/>
      <path class="band band--ember" fill="var(--band-ember)" d="M0,158 Q620,178 844,582 L844,1200 L0,1200 Z"/>
      <path class="field" role="img" aria-label="Dunkles Feld mit feinem Kreuzmuster" fill="var(--field)" d="M0,194 Q620,215 844,655 L844,1200 L0,1200 Z"/>
    </svg>

    <section class="medallion">
      <h1 class="medallion__title">Dunkle<br>Gedichte</h1>
      <div class="medallion__rule"></div>
      <p class="medallion__author">Jonas Wendler</p>
    </section>
  </main>
</body>
</html>
```